Orvane Thinner Logo and Packaging Design

We are seeking a striking and professional logo and packaging design for our new product line, Orvane Thinner. This logo will be used on the packaging for three different sizes of half-transparent carboys: 1L, 4L, and 20L. Orvane Thinner is a high-quality solvent brand known for its excellent solvency, fast-drying properties, and pleasant smell. The logo should feature an eagle motif to symbolize power and precision, and our slogan, "SOAR WITH PURITY." The design should be suitable for placement on hardware store and warehouse shelves. Additionally, we need the designer to create an eagle logo to accompany the packaging.

Packaging Dimensions:
1L Carboy:
Front: 71mm height x 142mm width
Side: 71mm height x 73mm width
4L Carboy:
Front: 160mm height x 170mm width
Side: 160mm height x 120mm width
20L Carboy:
Front: 245mm height x 190mm width
Side: 215mm height x 190mm width
Front Label Requirements:

Product Name: Thinner QXR
Volume: 20L
Precautionary Statements:
Keep Away from Sources of ignition - No Smoking
Avoid Contact with Eyes
Do Not Empty into Drains or Sewers
Take Precautionary Measures Against Static Discharge
Hazard Statements:
Flammable Liquid and Vapor
May be fatal if swallowed or enters Airways
Causes Skin Irritation
Causes Serious Eye Irritation
Causes Damage to Organs if Prolonged or Repeated Exposure
Hazard Pictograms: (Include relevant hazard symbols)
Design Requirements:

Logo: Eagle motif (to be designed by the designer)
Slogan: SOAR WITH PURITY
Color Scheme: Designer to recommend (should be striking and professional for retail display)

Please see my latest picture. Kindly note the packaging is in Plastic Carboy (not in metal tin as per PS).

Eagle to be more majestic and bigger (as if soaring in the sky).
Singapore landscape as background to have Singapore identity such as KTR, Corvale wheel, terrace at the cove etc.

Eagle to be more majestic and bigger, wings to spread wide.
We not want it to be of photo style, but more on a cartoon style. Please see my latest file uploaded.

Target Market(s)

Our target market includes painting companies, construction companies, direct household consumers, and industrial users who require high-quality solvents for various applications.

Industry/Entity Type

Chemical, spray paint and painting, household, industrial

Requirements
Must have
• Professional and Striking Design: Eye-catching and professional packaging for retail shelves. Eagle Logo: A strong, precise eagle logo. Slogan: "SOAR WITH PURITY" prominently displayed. Clear Precautionary and Hazard Statements: Important safety information and pictograms. Volume Indication: Clearly marked (e.g., 1L, 4L, 20L). Eagle to be more majestic and bigger (as if soaring in the sky). Singapore landscape as background to have Singapore identity such as KTR, Corvale wheel, terrace at the cove etc.
Nice to have
• Color Scheme Recommendations: Suggestions for a professional, striking color scheme. Versatility: Design elements adaptable across different sizes of packaging. Environmentally Friendly Elements: Indications of sustainability or eco-friendliness in the design.
Should not have
• Overly Complex Designs: Avoid cluttered or overly intricate designs that detract from readability. Inconsistent Branding: Ensure all elements are cohesive and align with the brand identity.

```html
<!DOCTYPE html>
<html lang="en">
<head>
<meta charset="utf-8">
<title>Orvane Thinner – 20L Label</title>
<link rel="stylesheet" href="https://fonts.googleapis.com/css2?family=Montserrat:wght@600;700;800&family=Open+Sans:wght@400;700&display=swap">
<style>
  :root {
    --bg: #e9e9ea;
    --label: #f2f2f2;
    --orange: #e4643a;
    --orange-deep: #d8552c;
    --ink: #2d2d2d;
    --white: #ffffff;
    --warn: #f2c20f;
    --pictogram-edge: #222222;
    --seam: #dadada;
  }
  * { box-sizing: border-box; margin: 0; padding: 0; }
  html, body { width: 1200px; height: 722px; overflow: hidden; }
  body {
    background: var(--bg);
    font-family: "Montserrat", sans-serif;
    color: var(--ink);
    display: flex;
    align-items: center;
    justify-content: center;
  }
  .label-panel {
    background: var(--label);
    height: 540px;
    position: relative;
    display: flex;
    flex-direction: column;
  }
  .side-panel { width: 250px; border-right: 1px solid var(--seam); }
  .front-panel { width: 440px; }

  .product-title {
    display: flex;
    align-items: center;
    gap: 10px;
    margin-top: 64px;
    font-weight: 700;
    white-space: nowrap;
  }
  .product-title .rule { height: 10px; background: var(--orange); }
  .side-panel .product-title { font-size: 15px; }
  .side-panel .product-title .rule:first-child { flex: 0 0 14px; }
  .side-panel .product-title .rule:last-child { flex: 1; }
  .front-panel .product-title { font-size: 24px; }
  .front-panel .product-title .rule:first-child { flex: 0 0 56px; }
  .front-panel .product-title .rule:last-child { flex: 0 0 56px; }

  .side-decor {
    margin-top: 40px;
    width: 130px;
    height: 130px;
    background: linear-gradient(135deg, var(--orange) 0%, var(--orange-deep) 100%);
    border-radius: 0 60px 0 0;
  }

  .brand {
    display: flex;
    flex-direction: column;
    align-items: center;
  }
  .brand-mark { border-radius: 50%; background: var(--orange); }
  .brand-name { font-weight: 700; letter-spacing: 0.06em; color: var(--ink); white-space: nowrap; }
  .slogan {
    background: var(--orange);
    color: var(--white);
    font-weight: 700;
    letter-spacing: 0.06em;
    border-radius: 0 0 22px 22px;
    text-align: center;
    white-space: nowrap;
  }
  .side-panel .brand { margin-top: 22px; }
  .side-panel .brand-mark { width: 30px; height: 30px; margin-bottom: 12px; }
  .side-panel .brand-name { font-size: 15px; }
  .side-panel .slogan { font-size: 11px; padding: 5px 14px; margin-top: 6px; }

  .front-panel .brand { margin-top: 58px; }
  .front-panel .brand-mark { width: 46px; height: 46px; margin-bottom: 22px; }
  .front-panel .brand-name { font-size: 22px; }
  .front-panel .slogan { font-size: 19px; padding: 9px 28px; margin-top: 14px; width: 268px; }

  .safety {
    display: flex;
    gap: 20px;
    margin: 44px 18px 0 18px;
    font-family: "Open Sans", sans-serif;
    font-size: 6.4px;
    line-height: 1.35;
  }
  .safety h3 { font-size: 7px; font-weight: 700; margin-bottom: 2px; }
  .safety ul { list-style: none; }
  .safety li::before { content: "• "; }

  .volume-band {
    margin-top: auto;
    margin-bottom: 24px;
    background: var(--orange);
    display: flex;
    align-items: center;
    color: var(--white);
    font-weight: 700;
  }
  .side-panel .volume-band { justify-content: center; font-size: 36px; height: 92px; }
  .front-panel .volume-band { justify-content: space-between; padding: 0 24px 0 20px; font-size: 50px; height: 100px; }
  .pictograms { display: flex; gap: 8px; }
</style>
</head>
<body>
  <section class="label-panel side-panel">
    <h2 class="product-title"><span class="rule"></span>THINNER QXR<span class="rule"></span></h2>
    <div class="side-decor" role="img" aria-label="Large orange sweeping wing decoration"></div>
    <div class="brand">
      <span class="brand-mark"></span>
      <span class="brand-name">ORVANE THINNER</span>
      <p class="slogan">SOAR WITH PURITY</p>
    </div>
    <div class="volume-band">20L</div>
  </section>

  <section class="label-panel front-panel">
    <h1 class="product-title"><span class="rule"></span>THINNER QXR<span class="rule"></span></h1>
    <div class="brand">
      <span class="brand-mark"></span>
      <span class="brand-name">ORVANE THINNER</span>
      <p class="slogan">SOAR WITH PURITY</p>
    </div>
    <div class="safety">
      <div class="safety-group">
        <h3>Precautionary</h3>
        <ul>
          <li>Keep Away from Sources of Ignition - No Smoking</li>
          <li>Avoid Contact with Eyes</li>
          <li>Do Not Empty into Drains or Sewers</li>
          <li>Take Precautionary Measures Against Static Discharge</li>
        </ul>
      </div>
      <div class="safety-group">
        <h3>Hazard</h3>
        <ul>
          <li>Flammable Liquid and Vapor</li>
          <li>May be fatal if swallowed or enters Airways</li>
          <li>Causes Skin Irritation</li>
          <li>Causes Serious Eye Irritation</li>
          <li>Causes Damage to Organs if Prolonged or Repeated Exposure</li>
        </ul>
      </div>
    </div>
    <div class="volume-band">
      <div class="pictograms">
        <svg width="38" height="34" viewBox="0 0 38 34" role="img" aria-label="Flammable hazard pictogram"><polygon points="19,2 36,32 2,32" fill="var(--warn)" stroke="var(--pictogram-edge)" stroke-width="2"/></svg>
        <svg width="38" height="34" viewBox="0 0 38 34" role="img" aria-label="Acute toxicity hazard pictogram"><polygon points="19,2 36,32 2,32" fill="var(--warn)" stroke="var(--pictogram-edge)" stroke-width="2"/></svg>
        <svg width="38" height="34" viewBox="0 0 38 34" role="img" aria-label="Health hazard pictogram"><polygon points="19,2 36,32 2,32" fill="var(--warn)" stroke="var(--pictogram-edge)" stroke-width="2"/></svg>
      </div>
      <span class="volume">20L</span>
    </div>
  </section>
</body>
</html>
```